Beekeeper needs a label for honey jars

Ciao! I'm from Como Italy
I'm a hobbyist beekeeper and I produce honey for myself and my friends.
I've named my apiary "Dado sereno," a play on words between my nickname (Dado, from Edoardo) and the Italian expression "Dado sereno," which translates to "a drizzle of honey" in English.
I need to create a label for my honey glass jars (250 gr and 500 gr).
I don't need a label for commercial purposes. I would like to include at least the name “Apicoltura Dado sereno", the type of honey (e.g., wildflower, acacia...) and a space for the production year, to be handwritten each year.
In the design some references to the world of bees.
For reference, attached a label with a style I like
Attached are the images of the selected jars and their measurements
Thanks and good job!

Target Market(s)

beekeeping, honey

Requirements
Nice to have
• I would like an elegant style with clean graphics.
Should not have
• Predominance of black color.

```html
<!DOCTYPE html>
<html lang="it">
<head>
<meta charset="utf-8">
<title>Apicoltura Dado sereno – Etichetta miele</title>
<link href="https://fonts.googleapis.com/css2?family=Barlow+Condensed:wght@500;600;700&display=swap" rel="stylesheet">
<style>
  :root {
    --bg: #ececec;
    --label: #ffffff;
    --stitch: #7a7a7a;
    --ink: #4a4a4a;
    --ink-soft: #6f6f6f;
    --honey: #e3a648;
    --honey-light: #f3d49c;
  }
  html, body {
    margin: 0;
    padding: 0;
    width: 1200px;
    height: 1185px;
    overflow: hidden;
    background: var(--bg);
  }
  .canvas {
    position: relative;
    width: 1200px;
    height: 1185px;
    font-family: "Barlow Condensed", "Arial Narrow", sans-serif;
  }
  .label-shape {
    position: absolute;
    inset: 0;
  }
  .text {
    position: absolute;
    left: 0;
    width: 1200px;
    text-align: center;
    margin: 0;
    line-height: 1;
    text-transform: uppercase;
  }
  .apiary-kind {
    top: 262px;
    font-size: 66px;
    font-weight: 600;
    color: var(--ink);
    letter-spacing: 0.5px;
  }
  .apiary-name {
    top: 336px;
    font-size: 130px;
    font-weight: 700;
    color: var(--honey);
    letter-spacing: 1px;
  }
  .emblem {
    position: absolute;
    left: 446px;
    top: 497px;
    width: 308px;
    height: 238px;
  }
  .place {
    top: 772px;
    font-size: 50px;
    font-weight: 500;
    color: var(--ink-soft);
    letter-spacing: 38px;
    padding-left: 38px;
    box-sizing: border-box;
  }
  .place-band {
    position: absolute;
    left: 488px;
    top: 820px;
    width: 224px;
    height: 28px;
    background: var(--honey);
    opacity: 0.85;
  }
  .variety {
    top: 880px;
    font-size: 66px;
    font-weight: 600;
    color: var(--ink-soft);
  }
  .fill-in {
    top: 1000px;
    font-size: 24px;
    font-weight: 600;
    color: var(--ink);
    letter-spacing: 3px;
  }
</style>
</head>
<body>
<div class="canvas">
  <svg class="label-shape" width="1200" height="1185" viewBox="0 0 1200 1185">
    <polygon points="90,592 318,116 882,116 1110,592 882,1068 318,1068" fill="var(--label)"/>
    <polygon points="115,592 333,140 867,140 1085,592 867,1044 333,1044" fill="none" stroke="var(--stitch)" stroke-width="5" stroke-dasharray="12 9"/>
  </svg>

  <p class="text apiary-kind">Apicoltura</p>
  <p class="text apiary-name">Dado sereno</p>

  <svg class="emblem" viewBox="0 0 308 238" role="img" aria-label="Emblema: ape stilizzata con goccia di miele">
    <defs>
      <radialGradient id="emblemTone" cx="50%" cy="45%" r="55%">
        <stop offset="0%" stop-color="var(--honey-light)"/>
        <stop offset="100%" stop-color="#ffffff"/>
      </radialGradient>
    </defs>
    <rect width="308" height="238" rx="20" fill="url(#emblemTone)"/>
  </svg>

  <p class="text place">Como</p>
  <div class="place-band" role="img" aria-label="Motivo ondulato del lago"></div>

  <p class="text variety">Millefiori</p>
  <p class="text fill-in">....GR | ....</p>
</div>
</body>
</html>
```